Letter and Envelope Design For Harborline Realty

Please design a letter and an envelope incorporating our logo (See Attached). We are also launched a business card contest. Since we want them to match, please feel free to submit a design for both the business card and also the letter design and envelope.

Requirements
Must have
• The envelope, the letter and the business cards must match somehow connecting the designs. We want them to have something that holds them together besides the logo.

```html
<!DOCTYPE html>
<html lang="en">
<head>
<meta charset="utf-8">
<title>Harborline Realty Stationery</title>
<link href="https://fonts.googleapis.com/css2?family=Montserrat:wght@500;600&family=Quicksand:wght@400;500;600&display=swap" rel="stylesheet">
<style>
:root{
  --navy:#2b2f8a;
  --ink:#2e2e33;
  --grey-band:#5a5a5e;
  --paper:#f4f4f5;
  --paper-shade:#e3e3e5;
  --canvas-light:#e4e4e5;
  --canvas-dark:#58585b;
  --card-black:#232325;
  --emboss:#3a3a3d;
}
*{margin:0;padding:0;box-sizing:border-box}
html,body{width:1200px;height:2494px;overflow:hidden}
body{position:relative;background:var(--canvas-light);font-family:"Quicksand",sans-serif;color:var(--ink)}
.stage-dark{position:absolute;left:0;top:1636px;width:1200px;height:858px;background:var(--canvas-dark)}
.sheet{position:absolute;box-shadow:0 3px 6px rgba(0,0,0,.25)}
.brand{display:flex;align-items:center;gap:10px}
.brand-ring{flex:none;border:3px solid var(--navy);border-radius:50%}
.brand-name{font-family:"Montserrat",sans-serif;font-weight:600;color:var(--navy);letter-spacing:2px;text-transform:uppercase;line-height:1.15;text-align:center;white-space:nowrap}
.brand-name span{display:block}
.foot-band{position:absolute;left:0;bottom:0;width:100%}

/* letter */
.letter{left:250px;top:170px;width:654px;height:840px;background:linear-gradient(180deg,var(--paper) 0%,var(--paper-shade) 35%,var(--paper) 100%)}
.letter .brand{position:absolute;left:36px;top:58px}
.letter .brand-ring{width:58px;height:58px}
.letter .brand-name{font-size:18px}
.letter-contact{position:absolute;top:64px;font-size:11.5px;line-height:18px;white-space:nowrap}
.letter-address{left:306px}
.letter-address b,.card-address b{color:var(--navy);font-weight:600}
.letter-rule{position:absolute;left:449px;top:66px;width:1px;height:50px;background:#999}
.letter-links{left:468px}
.icon-row{display:flex;align-items:center;gap:6px;white-space:nowrap}
.icon-row svg{flex:none;width:10px;height:10px;fill:var(--navy)}
.letter-recipient{position:absolute;left:36px;top:232px;font-size:13px;line-height:21px}
.recipient-name{font-weight:600;color:var(--navy);font-size:14px}
.letter-date{position:absolute;right:36px;top:234px;font-size:13px;font-weight:500}
.letter-body{position:absolute;left:36px;top:344px;width:582px;font-size:12.6px;line-height:22px;text-align:justify}
.letter-body p+p{margin-top:22px}
.letter-sign{position:absolute;left:36px;top:630px;font-size:11px}
.signature{display:block;width:96px;height:34px;margin:8px 0 6px;background:linear-gradient(90deg,#d6d6da,#e8e8ea)}
.signer{font-size:12px}

/* envelopes */
.envelope{top:1216px;width:508px;height:226px;background:#fff}
.env-front{left:80px}
.env-front .brand{position:absolute;left:30px;top:30px;gap:7px}
.env-front .brand-ring{width:38px;height:38px;border-width:2px}
.env-front .brand-name{font-size:11px;letter-spacing:1.5px}
.env-address{position:absolute;left:40px;top:156px;padding-left:10px;border-left:2px solid var(--navy);font-size:8.5px;line-height:14px}
.env-back{left:615px}
.env-flap{position:absolute;left:0;top:0;width:508px;height:94px}

/* business cards */
.card{top:1850px;width:440px;height:254px}
.card-back{left:110px;background:var(--card-black);display:flex;align-items:center;justify-content:center}
.card-back .brand-ring{width:70px;height:70px;border-color:var(--emboss)}
.card-back .brand-name{color:var(--emboss);font-size:22px}
.card-front{left:650px;background:#ececee}
.card-front .brand{position:absolute;left:28px;top:104px;gap:8px}
.card-front .brand-ring{width:44px;height:44px}
.card-front .brand-name{font-size:14px;letter-spacing:1.5px}
.card-divider{position:absolute;left:230px;top:46px;width:1px;height:150px;background:#8a8a8e}
.card-details{position:absolute;left:246px;top:50px;font-size:10.5px;line-height:16px}
.card-person{font-family:"Montserrat",sans-serif;font-weight:600;color:var(--navy);font-size:15px;letter-spacing:.5px}
.card-role{margin-bottom:4px}
</style>
</head>
<body>

<div class="stage-dark"></div>

<section class="sheet letter">
  <div class="brand"><span class="brand-ring"></span><span class="brand-name"><span>Harborline</span><span>Realty</span></span></div>
  <div class="letter-contact letter-address"><b>Harborline</b><br>418 Bayview Ave. Ste 210<br>Portside, VA 23999</div>
  <span class="letter-rule"></span>
  <div class="letter-contact letter-links">
    <div class="icon-row"><svg viewBox="0 0 10 10"><path d="M2 0l2 2-1 1.5c.8 1.6 1.9 2.7 3.5 3.5L8 6l2 2-1.5 2C4 9.5.5 6 0 1.5z"/></svg>+1 555 014 2290</div>
    <div class="icon-row"><svg viewBox="0 0 10 10"><path d="M0 2h10v6H0zM1 3v.4l4 2.6 4-2.6V3z"/></svg>info@harborlinerealty.com</div>
    <div class="icon-row"><svg viewBox="0 0 10 10"><circle cx="5" cy="5" r="5"/></svg>www.harborlinerealty.com</div>
  </div>
  <div class="letter-recipient"><div class="recipient-name">Daniel Orwell</div><div>Manager</div><div style="margin-top:4px">12 Rue des Mâts<br>31000 Belvarre</div></div>
  <div class="letter-date">Date: 12/11/2018</div>
  <div class="letter-body">
    <p>Lorem ipsum dolor sit amet, consectetuer adipiscing elit, sed diam nonummy nibh euismod tincidunt ut laoreet dolore magna aliquam erat volutpat. Ut wisi enim ad minim veniam, quis nostrud exerci tation ullamcorper suscipit lobortis nisl ut aliquip ex ea commodo consequat. Lorem ipsum dolor sit amet, cons ectetuer adipiscing elit, sed diam nonummy nibh euismod tincidunt ut laoreet dolore magna aliquam erat volutpat. Ut wisi enim ad minim veniam,</p>
    <p>quis nostrud exerci tation ullamcorper suscipit lobortis nisl ut aliquip ex ea commodo consequat. Lorem ipsum dolor sit amet, consectetuer adipiscing elit, sed diam nonummy nibh euismod tincidunt ut laoreet dolore magna aliquam erat volutpat. Ut wisi enim ad minim veniam, consequat. Duis autem vel eum iriure dolor in hendrerit in vulputate velit esse molestie consequat, vel illum dolore eu feugiat nulla facilisis at vero eros et accumsan .</p>
  </div>
  <div class="letter-sign">sincerely<span class="signature" role="img" aria-label="Handwritten signature"></span><span class="signer">Daniel Orwell</span></div>
  <svg class="foot-band" width="654" height="10" viewBox="0 0 654 10"><polygon points="0,0 330,0 322,10 0,10" fill="var(--navy)"/><polygon points="336,0 654,0 654,10 328,10" fill="var(--grey-band)"/></svg>
</section>

<section class="sheet envelope env-front">
  <div class="brand"><span class="brand-ring"></span><span class="brand-name"><span>Harborline</span><span>Realty</span></span></div>
  <div class="env-address"><b style="color:var(--navy)">Harborline</b><br>418 Bayview Ave. Ste 210<br>Portside, VA 23999</div>
  <svg class="foot-band" width="508" height="8" viewBox="0 0 508 8"><polygon points="0,0 256,0 250,8 0,8" fill="var(--navy)"/><polygon points="260,0 508,0 508,8 254,8" fill="var(--grey-band)"/></svg>
</section>

<section class="sheet envelope env-back">
  <svg class="env-flap" viewBox="0 0 508 94"><path d="M0 0H508L502 60Q500 74 486 74L270 88Q254 92 238 88L22 74Q10 74 8 60Z" fill="var(--navy)"/></svg>
</section>

<section class="sheet card card-back">
  <div class="brand"><span class="brand-ring"></span><span class="brand-name"><span>Harborline</span><span>Realty</span></span></div>
</section>

<section class="sheet card card-front">
  <div class="brand"><span class="brand-ring"></span><span class="brand-name"><span>Harborline</span><span>Realty</span></span></div>
  <span class="card-divider"></span>
  <div class="card-details">
    <div class="card-person">DANIEL ORWELL</div>
    <div class="card-role">Resident Manager</div>
    <div>418 Bayview Ave. Ste 210</div>
    <div>Portside, VA 23999</div>
    <div class="icon-row" style="margin-top:4px"><svg viewBox="0 0 10 10"><path d="M2 0l2 2-1 1.5c.8 1.6 1.9 2.7 3.5 3.5L8 6l2 2-1.5 2C4 9.5.5 6 0 1.5z"/></svg>+1 555 014 2290</div>
    <div class="icon-row"><svg viewBox="0 0 10 10"><path d="M0 2h10v6H0zM1 3v.4l4 2.6 4-2.6V3z"/></svg>info@harborlinerealty.com</div>
    <div class="icon-row"><svg viewBox="0 0 10 10"><circle cx="5" cy="5" r="5"/></svg>www.harborlinerealty.com</div>
  </div>
  <svg class="foot-band" width="440" height="8" viewBox="0 0 440 8"><polygon points="0,0 280,0 274,8 0,8" fill="var(--navy)"/><polygon points="284,0 440,0 440,8 278,8" fill="var(--grey-band)"/></svg>
</section>

</body>
</html>
```